Vorlanta PowerPoint Template

I have a company called Vorlanta, LLC and my company logo is already designed. I need a PowerPoint template that I will be using to pitch potential investors and business partners. This should be a very professional-looking template that leverages the company logo colors and really pops. The company is an AI product research and development company.

```html
<!DOCTYPE html>
<html lang="en">
<head>
<meta charset="UTF-8">
<title>Vorlanta Investor Pitch Template</title>
<link href="https://fonts.googleapis.com/css2?family=Poppins:wght@400;500;600;700&display=swap" rel="stylesheet">
<style>
:root{
  --red:#b5121b;
  --red-deep:#9e0f17;
  --ink:#2e2e2e;
  --ink-soft:#555;
  --charcoal:#1c1c1c;
  --slate:#3a3a3a;
  --dark-slide:#343434;
  --paper:#f5f5f5;
  --white:#ffffff;
  --stage:#000000;
}
*{margin:0;padding:0;box-sizing:border-box}
html,body{width:995px;height:1200px;overflow:hidden;background:var(--stage)}
body{position:relative;font-family:'Poppins',sans-serif;color:var(--ink)}
.abs{position:absolute}
.slide{position:absolute;width:435px;height:245px;overflow:hidden}
.slide--light{background:radial-gradient(ellipse at 75% 20%,#ffffff 0%,var(--paper) 55%,#ececec 100%)}
.slide--dark{background:radial-gradient(ellipse at 70% 40%,#3d3d3d 0%,var(--dark-slide) 60%,#2a2a2a 100%)}
.slide--red{background:radial-gradient(ellipse at 40% 30%,#c8161f 0%,var(--red) 55%,var(--red-deep) 100%)}
.col-left{left:38px}.col-right{left:504px}
.row-1{top:39px}.row-2{top:324px}.row-3{top:610px}.row-4{top:895px}

.brand{position:absolute;top:8px;right:28px;display:flex;align-items:center;gap:4px;font-weight:500;font-size:14px;letter-spacing:-0.4px;color:var(--ink)}
.brand__mark{width:15px;height:15px;border-radius:50%;background:var(--red)}
.slide--dark .brand,.slide--red .brand{color:var(--white)}
.slide--red .brand__mark{background:var(--white)}

.footer{position:absolute;left:0;bottom:0;width:100%;height:14px;background:var(--red);color:var(--white);font-size:4.6px;display:flex;align-items:center;justify-content:space-between;padding:0 28px}
.footer--open{background:transparent;border:none}
.footer span::before{content:"";display:inline-block;width:3.5px;height:3.5px;border-radius:50%;background:var(--white);margin-right:2px;vertical-align:-0.3px}

.marker{position:absolute;width:10px;height:10px;border-radius:50%;background:var(--red)}
.title{position:absolute;font-weight:700;font-size:17px;line-height:1;white-space:nowrap}
.title .accent{color:var(--red)}
.title .muted{color:var(--ink-soft)}
.copy{position:absolute;font-size:4.3px;line-height:8.1px;color:var(--ink-soft)}
.label{font-weight:700;font-size:4.8px;letter-spacing:0.1px;margin-bottom:4px}
.photo{position:absolute}

.card{position:absolute;padding:10px 11px;font-size:3.9px;line-height:6.8px}
.card--dark{background:var(--charcoal);color:#ddd}
.card--slate{background:var(--slate);color:#ddd;border-radius:8px}
.card--white{background:var(--white);color:var(--ink-soft);border-radius:8px;box-shadow:0 2px 8px rgba(0,0,0,.1)}
.card--red{background:var(--red);color:#f3dcdc}
.card .label{color:var(--white)}
.card--white .label{color:var(--red)}

.service{position:absolute;width:85px;height:74px;border:0.8px solid #9a9a9a;border-radius:2px;padding:11px 6px;font-size:3.9px;line-height:6.8px;color:#ddd}
.service--active{background:var(--red);border-color:var(--red)}
.service__dot{width:5px;height:5px;border-radius:50%;background:var(--white);margin-bottom:4px}
.service .label{color:var(--white);margin-bottom:3px}

.stat{position:absolute}
.stat__num{color:var(--red);font-weight:600;font-size:10px;line-height:1}
.stat__cap{font-size:4.8px;color:var(--ink);margin-top:3px}

.step{position:absolute;left:243px;display:flex;gap:8px}
.step__icon{width:24px;height:24px;border-radius:50%;flex:none;display:flex;align-items:center;justify-content:center}
.step__icon--dark{background:#3a3a3a}
.step__icon--red{background:var(--red)}
.step__title{font-weight:700;font-size:5.2px;margin-bottom:2px}
.step__text{font-size:4.3px;line-height:8px;color:var(--ink-soft);width:145px}

.connector{position:absolute;height:0.7px;background:#555}
.dot{position:absolute;width:5px;height:5px;border-radius:50%;background:var(--ink)}
.vline{position:absolute;width:0.7px;background:#888}

.member__name{position:absolute;font-weight:700;font-size:5.2px}
.member__role{position:absolute;font-size:5.2px;color:var(--red)}
</style>
</head>
<body>

<!-- Slide 1: Cover -->
<section class="slide slide--light col-left row-1">
  <div class="brand"><span class="brand__mark"></span>Vorlanta</div>
  <div class="abs" style="left:32px;top:51px;width:142px;height:142px;border-radius:50%;border:0.8px solid var(--red)"></div>
  <div class="photo" role="img" aria-label="Glowing AI sphere held above an open hand" style="left:38px;top:57px;width:130px;height:130px;border-radius:50%;background:radial-gradient(circle at 50% 45%,#2c7fb0 0%,#0f3550 40%,#08121c 80%)"></div>
  <div class="abs" style="left:24px;top:51px;width:44px;height:44px;border-radius:50%;background:#3a3a3a;border:2px solid var(--white);color:var(--white);text-align:center;padding-top:6px">
    <div style="font-weight:700;font-size:14px;line-height:1">20</div>
    <div style="font-size:4.3px;line-height:5px">years<br>Experience</div>
  </div>
  <div class="abs" style="left:126px;top:163px;width:40px;height:40px;border-radius:50%;border:0.8px solid var(--red);padding:3px"><div style="width:100%;height:100%;border-radius:50%;background:var(--red)"></div></div>
  <div class="photo" role="img" aria-label="Futuristic aircraft silhouette" style="left:217px;top:60px;width:42px;height:17px;border-radius:9px;background:linear-gradient(90deg,#0d1420,#2b3d55,#0d1420)"></div>
  <div class="title accent" style="left:264px;top:59px;color:var(--red)">Revolutionizing</div>
  <div class="title" style="left:216px;top:82px;color:var(--slate)">Innovation with AI</div>
  <p class="copy" style="left:217px;top:108px;width:162px">Lorem ipsum dolor sit amet, consectetur adipiscing elit, sed do eiusmod tempor incididunt ut labore et dolore magna aliqua. Ut enim ad minim veniam, quis nostrud exercitation ullamco laboris nisi ut aliquip ex ea commodo consequat.</p>
  <div class="abs" style="left:218px;top:149px;width:1.5px;height:14px;background:var(--red)"></div>
  <p class="copy" style="left:226px;top:146px;width:150px">Lorem ipsum dolor sit amet, consectetur adipiscing elit, sed do eiusmod tempor incididunt ut labore et dolore.</p>
  <div class="abs" style="left:342px;top:177px;width:100px;height:41px;border-radius:21px 0 0 21px;border:0.8px solid #999"></div>
  <div class="photo" role="img" aria-label="AI chip glowing over a night city" style="left:345px;top:180px;width:95px;height:35px;border-radius:18px 0 0 18px;background:linear-gradient(90deg,#0c1a2e,#1f4f80 50%,#7a4a1a 70%,#0c1a2e)"></div>
  <footer class="footer"><span>www.vorlanta.com</span><span>contact@vorlanta.com</span></footer>
</section>

<!-- Slide 2: About Us -->
<section class="slide slide--light col-right row-1">
  <div class="brand"><span class="brand__mark"></span>Vorlanta</div>
  <span class="marker" style="left:28px;top:17px"></span>
  <div class="title accent" style="left:27px;top:31px;color:var(--red)">About Us</div>
  <div class="card card--dark" style="left:27px;top:58px;width:177px;height:69px">
    <div class="label">HEADING</div>
    Lorem ipsum dolor sit amet, consectetur adipiscing elit, sed do eiusmod tempor incididunt ut labore et dolore magna aliqua. Ut enim ad minim veniam, quis nostrud exercitation ullamco laboris nisi ut aliquip ex ea commodo consequat.
  </div>
  <div class="connector" style="left:204px;top:89.5px;width:22px"></div>
  <span class="dot" style="left:224px;top:87px"></span>
  <div class="stat" style="left:57px;top:140px"><div class="stat__num">250 K</div><div class="stat__cap">Lorum Ipsum</div></div>
  <div class="stat" style="left:114px;top:140px"><div class="stat__num">100 +</div><div class="stat__cap">Lorum Ipsum</div></div>
  <div class="stat" style="left:168px;top:140px"><div class="stat__num">5 K</div><div class="stat__cap">Lorum Ipsum</div></div>
  <p class="copy" style="left:57px;top:169px;width:162px">Lorem ipsum dolor sit amet, consectetur adipiscing elit, sed do eiusmod tempor incididunt ut labore et dolore magna aliqua. Ut enim ad minim veniam, quis nostrud exercitation ullamco laboris nisi ut aliquip ex ea commodo consequat.</p>
  <div class="abs" style="left:255px;top:54px;width:152px;height:152px;border-radius:50%;border:0.8px solid var(--red)"></div>
  <div class="photo" role="img" aria-label="Engineers working at a holographic control screen" style="left:262px;top:61px;width:138px;height:138px;border-radius:50%;background:radial-gradient(circle at 40% 45%,#3f7fb3 0%,#1a3d5e 45%,#0b1724 85%)"></div>
  <footer class="footer"><span>www.vorlanta.com</span><span>contact@vorlanta.com</span></footer>
</section>

<!-- Slide 3: Vision & Mission -->
<section class="slide slide--light col-left row-2">
  <div class="brand"><span class="brand__mark"></span>Vorlanta</div>
  <div class="abs" style="left:27px;top:41px;width:1.5px;height:10px;background:var(--red)"></div>
  <div class="abs" style="left:33px;top:43px;font-weight:700;font-size:5.2px;color:var(--red)">VISION</div>
  <p class="copy" style="left:27px;top:56px;width:163px">Lorem ipsum dolor sit amet, consectetur adipiscing elit, sed do eiusmod tempor incididunt ut labore et dolore magna aliqua. Ut enim ad minim veniam, quis nostrud exercitation ullamco laboris nisi ut aliquip ex ea commodo consequat.</p>
  <span class="marker" style="left:46px;top:122px"></span>
  <div class="title" style="left:45px;top:137px;color:var(--red)">Vision</div>
  <div class="title" style="left:45px;top:157px;color:var(--slate)">&amp; Mission</div>
  <div class="card card--slate" style="left:207px;top:36px;width:153px;height:53px"><div class="label">MISSION 1</div>Lorem ipsum dolor sit amet, consectetur adipiscing elit, sed do eiusmod tempor incididunt ut labore et dolore magna aliqua. Ut enim ad minim veniam, quis nostrud</div>
  <div class="card card--white" style="left:224px;top:98px;width:153px;height:53px"><div class="label">MISSION 2</div>Lorem ipsum dolor sit amet, consectetur adipiscing elit, sed do eiusmod tempor incididunt ut labore et dolore magna aliqua. Ut enim ad minim veniam, quis nostrud</div>
  <div class="card card--white" style="left:253px;top:159px;width:153px;height:53px"><div class="label">MISSION 3</div>Lorem ipsum dolor sit amet, consectetur adipiscing elit, sed do eiusmod tempor incididunt ut labore et dolore magna aliqua. Ut enim ad minim veniam, quis nostrud</div>
  <footer class="footer"><span>www.vorlanta.com</span><span>contact@vorlanta.com</span></footer>
</section>

<!-- Slide 4: Our Services -->
<section class="slide slide--dark col-right row-2">
  <div class="brand"><span class="brand__mark"></span>Vorlanta</div>
  <div class="photo" role="img" aria-label="Portrait in profile wearing glasses reflecting blue data" style="left:28px;top:23px;width:97px;height:172px;border-radius:49px;background:radial-gradient(ellipse at 40% 45%,#3a6f9c 0%,#17304a 50%,#0a1420 90%)"></div>
  <span class="marker" style="left:138px;top:44px"></span>
  <div class="title" style="left:137px;top:59px;color:var(--white)">Our Services</div>
  <div class="service" style="left:138px;top:100px"><div class="service__dot"></div><div class="label">HEADING</div>Lorem ipsum dolor sit amet, consectetur adipiscing elit, sed do eiusmod tempor incididunt ut labore et dolore magna aliqua. Ut enim ad minim veniam, quis</div>
  <div class="service service--active" style="left:230px;top:100px"><div class="service__dot"></div><div class="label">HEADING</div>Lorem ipsum dolor sit amet, consectetur adipiscing elit, sed do eiusmod tempor incididunt ut labore et dolore magna aliqua. Ut enim ad minim veniam, quis</div>
  <div class="service" style="left:321px;top:100px"><div class="service__dot"></div><div class="label">HEADING</div>Lorem ipsum dolor sit amet, consectetur adipiscing elit, sed do eiusmod tempor incididunt ut labore et dolore magna aliqua. Ut enim ad minim veniam, quis</div>
  <footer class="footer"><span>www.vorlanta.com</span><span>contact@vorlanta.com</span></footer>
</section>

<!-- Slide 5: Our Process -->
<section class="slide slide--light col-left row-3">
  <div class="brand"><span class="brand__mark"></span>Vorlanta</div>
  <div class="photo" role="img" aria-label="Glowing digital brain inside a server corridor" style="left:27px;top:40px;width:177px;height:82px;border-radius:41px;background:radial-gradient(circle at 45% 50%,#c8402a 0%,#3a3040 25%,#14324f 55%,#0a1626 90%)"></div>
  <span class="marker" style="left:28px;top:133px"></span>
  <div class="title" style="left:27px;top:148px;color:var(--red)">Our Process</div>
  <p class="copy" style="left:27px;top:168px;width:163px">Lorem ipsum dolor sit amet, consectetur adipiscing elit, sed do eiusmod tempor incididunt ut labore et dolore magna aliqua. Ut enim ad minim veniam, quis nostrud exercitation ullamco laboris nisi ut aliquip ex ea commodo consequat.</p>
  <div class="step" style="top:34px"><div class="step__icon step__icon--dark"><svg width="12" height="12" viewBox="0 0 12 12" fill="none" stroke="#fff" stroke-width="0.8"><circle cx="6" cy="6" r="4.5"/><circle cx="6" cy="6" r="1.5"/></svg></div><div><div class="step__title">PROCESS 1</div><div class="step__text">Lorem ipsum dolor sit amet, consectetur adipiscing elit, sed do eiusmod tempor incididunt ut labore et</div></div></div>
  <div class="step" style="top:72px"><div class="step__icon step__icon--red"><svg width="12" height="12" viewBox="0 0 12 12" fill="none" stroke="#fff" stroke-width="0.8"><circle cx="6" cy="6" r="4.5"/><path d="M3 6h6M6 3v6"/></svg></div><div><div class="step__title">PROCESS 2</div><div class="step__text">Lorem ipsum dolor sit amet, consectetur adipiscing elit, sed do eiusmod tempor incididunt ut labore et</div></div></div>
  <div class="step" style="top:110px"><div class="step__icon step__icon--dark"><svg width="12" height="12" viewBox="0 0 12 12" fill="none" stroke="#fff" stroke-width="0.8"><rect x="3" y="3" width="6" height="6"/><path d="M4.5 1v2M7.5 1v2M4.5 9v2M7.5 9v2M1 4.5h2M1 7.5h2M9 4.5h2M9 7.5h2"/></svg></div><div><div class="step__title">PROCESS 3</div><div class="step__text">Lorem ipsum dolor sit amet, consectetur adipiscing elit, sed do eiusmod tempor incididunt ut labore et</div></div></div>
  <div class="step" style="top:148px"><div class="step__icon step__icon--red"><svg width="12" height="12" viewBox="0 0 12 12" fill="none" stroke="#fff" stroke-width="0.8"><circle cx="6" cy="6" r="4.5"/><path d="M6 1.5v9"/></svg></div><div><div class="step__title">PROCESS 4</div><div class="step__text">Lorem ipsum dolor sit amet, consectetur adipiscing elit, sed do eiusmod tempor incididunt ut labore et</div></div></div>
  <div class="step" style="top:186px"><div class="step__icon step__icon--red"><svg width="12" height="12" viewBox="0 0 12 12" fill="none" stroke="#fff" stroke-width="0.8"><rect x="2.5" y="2.5" width="7" height="7" rx="1"/><path d="M4.5 5h3M4.5 7h3"/></svg></div><div><div class="step__title">PROCESS 4</div><div class="step__text">Lorem ipsum dolor sit amet, consectetur adipiscing elit, sed do eiusmod tempor incididunt ut labore et</div></div></div>
  <footer class="footer"><span>www.vorlanta.com</span><span>contact@vorlanta.com</span></footer>
</section>

<!-- Slide 6: Core Values -->
<section class="slide slide--light col-right row-3">
  <div class="brand"><span class="brand__mark"></span>Vorlanta</div>
  <span class="marker" style="left:28px;top:17px"></span>
  <div class="title" style="left:27px;top:31px"><span class="accent">Core</span> <span style="color:var(--slate)">Values</span></div>
  <p class="copy" style="left:28px;top:52px;width:92px;line-height:6.9px;font-size:3.9px">Lorem ipsum dolor sit amet, consectetur adipiscing elit, sed do eiusmod tempor incididunt ut labore et dolore magna aliqua. Ut enim ad minim veniam,</p>
  <span class="dot" style="left:95px;top:102.5px"></span>
  <div class="connector" style="left:100px;top:104.7px;width:25px"></div>
  <div class="card card--dark" style="left:125px;top:76px;width:148px;height:57px;border-radius:2px"><div class="label">CORE VALUE 1</div>Lorem ipsum dolor sit amet, consectetur adipiscing elit, sed do eiusmod tempor incididunt ut labore et dolore magna aliqua. Ut enim ad minim veniam, quis nostrud exercitation ullamco laboris nisi ut aliquip ex ea commodo consequat.</div>
  <div class="card card--red" style="left:288px;top:76px;width:147px;height:57px;border-radius:2px 0 0 2px"><div class="label">CORE VALUE 2</div>Lorem ipsum dolor sit amet, consectetur adipiscing elit, sed do eiusmod tempor incididunt ut labore et dolore magna aliqua. Ut enim ad minim veniam, quis nostrud exercitation ullamco laboris nisi ut aliquip ex ea commodo consequat.</div>
  <div class="connector" style="left:0;top:178.7px;width:29px"></div>
  <div class="card card--red" style="left:29px;top:150px;width:148px;height:57px;border-radius:2px"><div class="label">CORE VALUE 3</div>Lorem ipsum dolor sit amet, consectetur adipiscing elit, sed do eiusmod tempor incididunt ut labore et dolore magna aliqua. Ut enim ad minim veniam, quis nostrud exercitation ullamco laboris nisi ut aliquip ex ea commodo consequat.</div>
  <div class="card card--dark" style="left:192px;top:150px;width:148px;height:57px;border-radius:2px"><div class="label">CORE VALUE 4</div>Lorem ipsum dolor sit amet, consectetur adipiscing elit, sed do eiusmod tempor incididunt ut labore et dolore magna aliqua. Ut enim ad minim veniam, quis nostrud exercitation ullamco laboris nisi ut aliquip ex ea commodo consequat.</div>
  <div class="connector" style="left:340px;top:178.7px;width:28px"></div>
  <span class="dot" style="left:367px;top:176.5px"></span>
  <footer class="footer"><span>www.vorlanta.com</span><span>contact@vorlanta.com</span></footer>
</section>

<!-- Slide 7: Our Team -->
<section class="slide slide--light col-left row-4">
  <div class="brand"><span class="brand__mark"></span>Vorlanta</div>
  <span class="marker" style="left:28px;top:17px"></span>
  <div class="title" style="left:27px;top:31px"><span class="accent">Our</span> <span style="color:var(--slate)">Team</span></div>

  <span class="dot" style="left:67px;top:67px"></span>
  <div class="vline" style="left:69px;top:70px;height:14px"></div>
  <div class="abs" style="left:29px;top:83px;width:81px;height:120px;border-radius:41px;border:0.8px solid var(--red)"></div>
  <div class="photo" role="img" aria-label="Portrait of team member in a navy blazer" style="left:32px;top:86px;width:75px;height:114px;border-radius:38px;background:linear-gradient(180deg,#9aa3ad 0%,#5f6b78 45%,#1f2d44 100%)"></div>
  <div class="vline" style="left:69px;top:203px;height:28px"></div>
  <div class="member__name" style="left:115px;top:109px">AREN HOLLIS</div>
  <div class="member__role" style="left:115px;top:119px">Manager of the Company</div>
  <p class="copy" style="left:115px;top:131px;width:97px;line-height:6.5px;font-size:4.1px">Lorem ipsum dolor sit amet, consectetur adipiscing elit, sed do eiusmod tempor incididunt ut labore et dolore magna aliqua. Ut enim ad minim veniam, quis nostrud exercitation ullamco laboris nisi ut aliquip ex ea commodo consequat.</p>

  <span class="dot" style="left:259px;top:67px"></span>
  <div class="vline" style="left:261px;top:70px;height:14px"></div>
  <div class="abs" style="left:221px;top:83px;width:81px;height:120px;border-radius:41px;border:0.8px solid var(--red)"></div>
  <div class="photo" role="img" aria-label="Portrait of team member in an office corridor" style="left:224px;top:86px;width:75px;height:114px;border-radius:38px;background:linear-gradient(180deg,#b7a48c 0%,#6e5e50 45%,#1f2a40 100%)"></div>
  <div class="vline" style="left:261px;top:203px;height:28px"></div>
  <div class="member__name" style="left:307px;top:109px">MIRA SOLEN</div>
  <div class="member__role" style="left:307px;top:119px">Manager of the Company</div>
  <p class="copy" style="left:307px;top:131px;width:97px;line-height:6.5px;font-size:4.1px">Lorem ipsum dolor sit amet, consectetur adipiscing elit, sed do eiusmod tempor incididunt ut labore et dolore magna aliqua. Ut enim ad minim veniam, quis nostrud exercitation ullamco laboris nisi ut aliquip ex ea commodo consequat.</p>
  <footer class="footer"><span>www.vorlanta.com</span><span>contact@vorlanta.com</span></footer>
</section>

<!-- Slide 8: Closing -->
<section class="slide slide--red col-right row-4">
  <div class="brand"><span class="brand__mark"></span>Vorlanta</div>
  <span class="abs" style="left:212px;top:88px;width:10px;height:10px;border-radius:50%;border:0.8px solid rgba(255,255,255,.6)"></span>
  <div class="title" style="left:0;width:100%;text-align:center;top:101px;color:var(--white)">Thank You for Your Time &amp; Interest</div>
  <div class="abs" style="left:0;width:100%;text-align:center;top:129px;font-weight:700;font-size:4.3px;color:var(--white)">WE'RE EXCITED TO BUILD THE FUTURE OF AI, TOGETHER.</div>
  <div class="abs" style="left:28px;top:228px;width:378px;height:0.6px;background:rgba(255,255,255,.5)"></div>
  <footer class="footer footer--open"><span>www.vorlanta.com</span><span>contact@vorlanta.com</span></footer>
</section>

</body>
</html>
```